Quillmere Capital LLC

Need Professional Business cards for New Investment Fund

Target Market(s)

High Quality investors

Industry/Entity Type

Financial

Contact Information for Business Card

Phone Number +1 555 284 6190
Name Lukas Varenko
Title Fund Manager
email lv@FundQuillmere.com
Website www.FundQuillmere.com

Colors

Designer to choose colors to be used in the design.

Requirements
Must have
• Must have our Logo and all of the above. Must be made so lettering and loge can be raised

```html
<!DOCTYPE html>
<html lang="en">
<head>
<meta charset="utf-8">
<title>Quillmere Capital – Business Cards</title>
<link href="https://fonts.googleapis.com/css2?family=Montserrat:wght@400;600&display=swap" rel="stylesheet">
<style>
  :root {
    --backdrop: #1c1c1c;
    --card: #222324;
    --card-edge: #2c2d2e;
    --silver: #c8c8c8;
    --silver-soft: #b4b4b4;
    --accent-green: #3ee023;
  }
  * { margin: 0; padding: 0; box-sizing: border-box; }
  html, body {
    width: 1200px;
    height: 900px;
    overflow: hidden;
    background: var(--backdrop);
    font-family: "Montserrat", sans-serif;
  }
  .canvas {
    position: relative;
    width: 1200px;
    height: 900px;
    background: radial-gradient(ellipse at 50% 40%, #2a2a2a 0%, var(--backdrop) 70%);
  }
  .card {
    position: absolute;
    left: 250px;
    width: 700px;
    height: 400px;
    background: linear-gradient(135deg, var(--card) 0%, #262728 60%, #2e2f30 100%);
    border: 1px solid var(--card-edge);
    box-shadow: 0 14px 30px rgba(0,0,0,0.55);
  }
  .card--front { top: 40px; }
  .card--back { top: 470px; }

  .wordmark {
    display: flex;
    align-items: center;
    gap: 12px;
    color: var(--silver);
    font-weight: 600;
    letter-spacing: 2px;
    text-transform: uppercase;
    white-space: nowrap;
  }
  .wordmark__mark {
    width: 20px;
    height: 20px;
    background: var(--silver);
    flex: none;
  }
  .card--front .wordmark {
    position: absolute;
    left: 50%;
    top: 50%;
    transform: translate(-50%, -50%);
    font-size: 40px;
  }
  .card--back .wordmark {
    position: absolute;
    left: 40px;
    top: 180px;
    font-size: 28px;
  }
  .card--back .wordmark__mark { width: 16px; height: 16px; }

  .divider {
    position: absolute;
    left: 318px;
    top: 70px;
    width: 3px;
    height: 260px;
    background: var(--accent-green);
  }
  .contact {
    position: absolute;
    left: 370px;
    top: 88px;
    color: var(--silver);
  }
  .contact__name {
    font-size: 24px;
    font-weight: 600;
    text-transform: uppercase;
    letter-spacing: 0.5px;
  }
  .contact__title {
    font-size: 18px;
    color: var(--silver-soft);
    margin-top: 2px;
  }
  .contact__address {
    font-size: 18px;
    line-height: 26px;
    color: var(--silver-soft);
    margin-top: 20px;
    letter-spacing: 0.8px;
  }
  .contact__list {
    list-style: none;
    margin-top: 18px;
    font-size: 18px;
    line-height: 28px;
    letter-spacing: 0.8px;
  }
  .contact__list li { display: flex; align-items: center; gap: 10px; white-space: nowrap; }
  .contact__list svg { width: 14px; height: 14px; flex: none; }
</style>
</head>
<body>
<main class="canvas">
  <section class="card card--front">
    <div class="wordmark"><span class="wordmark__mark"></span>Quillmere</div>
  </section>

  <section class="card card--back">
    <div class="wordmark"><span class="wordmark__mark"></span>Quillmere</div>
    <div class="divider"></div>
    <div class="contact">
      <p class="contact__name">Lukas Varenko</p>
      <p class="contact__title">Fund Manager</p>
      <p class="contact__address">14 Alder st.<br>Millbrook, NJ, 08555</p>
      <ul class="contact__list">
        <li>
          <svg viewBox="0 0 16 16" fill="var(--silver)"><path d="M3.5 1h2.5l1 3.5-1.6 1.2a8 8 0 0 0 4.9 4.9L11.5 9 15 10v2.5c0 .8-.7 1.5-1.5 1.5C7 14 2 9 2 2.5 2 1.7 2.7 1 3.5 1z"/></svg>
          +1 555 284 6190
        </li>
        <li>
          <svg viewBox="0 0 16 16" fill="none" stroke="var(--silver)" stroke-width="1.5"><rect x="1.5" y="3.5" width="13" height="9"/><path d="M1.5 3.5 8 9l6.5-5.5"/></svg>
          lv@FundQuillmere.com
        </li>
        <li>
          <svg viewBox="0 0 16 16" fill="none" stroke="var(--silver)" stroke-width="1.3"><circle cx="8" cy="8" r="6.5"/><ellipse cx="8" cy="8" rx="3" ry="6.5"/><path d="M1.5 8h13M2.5 5h11M2.5 11h11"/></svg>
          www.FundQuillmere.com
        </li>
      </ul>
    </div>
  </section>
</main>
</body>
</html>
```